Local Roofing/Construction company business needs new biz card design

We need a new business card design, current cards are from the start of this operation and generic at best. We are a local Construction Company (General Contractor) with a majority of our work originating from insurance claims-exterior finish work is the main focus (Roofs-Siding-Gutters etc). Heavily involved with homeowners and the low ball offers they receive from insurance company's after a insurable event takes place. I have attached some of our original logo file(s) below.

```html
<!DOCTYPE html>
<html lang="en">
<head>
<meta charset="utf-8">
<title>Ridgeway Construction — Business Card</title>
<link href="https://fonts.googleapis.com/css2?family=Montserrat:wght@400;700&display=swap" rel="stylesheet">
<style>
  :root {
    --ink: #0f1f23;
    --green: #52b56d;
    --white: #ffffff;
    --text-light: #e6ecec;
    --backdrop: #d6d5d2;
  }
  * { margin: 0; padding: 0; box-sizing: border-box; }
  html, body { width: 1200px; height: 801px; overflow: hidden; }
  body {
    background: var(--backdrop);
    font-family: "Montserrat", Arial, sans-serif;
    position: relative;
  }
  .card {
    position: absolute;
    top: 252px;
    width: 525px;
    height: 300px;
    background: var(--ink);
    border: 3px solid var(--green);
    border-top-width: 1px;
    border-right-width: 1px;
    overflow: hidden;
    display: flex;
  }
  .card--front { left: 50px; }
  .card--back { left: 625px; align-items: center; justify-content: center; }

  .front__brand {
    width: 32%;
    background: var(--white);
    display: flex;
    align-items: center;
    justify-content: center;
  }
  .front__info {
    flex: 1;
    padding: 46px 30px 0 34px;
    color: var(--text-light);
  }
  .wordmark {
    display: flex;
    align-items: center;
    gap: 8px;
    color: var(--green);
    font-weight: 700;
    text-transform: uppercase;
    line-height: 1.05;
  }
  .wordmark__square { background: var(--green); flex: none; }
  .wordmark--small { font-size: 15px; }
  .wordmark--small .wordmark__square { width: 16px; height: 16px; }
  .wordmark--large { font-size: 30px; gap: 14px; }
  .wordmark--large .wordmark__square { width: 30px; height: 30px; }

  .person__name {
    color: var(--green);
    font-weight: 700;
    font-size: 21px;
    letter-spacing: 0.5px;
    text-transform: uppercase;
  }
  .person__role { font-size: 12.5px; margin-top: 2px; }
  .divider {
    height: 1px;
    background: var(--green);
    margin: 12px 0;
    width: 92%;
  }
  .address { font-size: 12.5px; line-height: 1.45; }
  .contact { list-style: none; font-size: 12.5px; line-height: 1.6; }
  .contact li { display: flex; align-items: center; gap: 8px; }
  .contact svg { width: 10px; height: 10px; flex: none; }
  .accent { color: var(--green); }
</style>
</head>
<body>
  <section class="card card--front">
    <div class="front__brand">
      <div class="wordmark wordmark--small">
        <span class="wordmark__square"></span>
        <span>Ridgeway<br>Construction</span>
      </div>
    </div>
    <div class="front__info">
      <h1 class="person__name">Calvin Marsh</h1>
      <p class="person__role">Managing Director</p>
      <div class="divider"></div>
      <p class="address">1480 W Harlow Avenue<br>Fenwick County Name 4187</p>
      <div class="divider"></div>
      <ul class="contact">
        <li><svg viewBox="0 0 10 10"><path d="M2 1l2 2-1 1.2c.6 1.2 1.6 2.2 2.8 2.8L7 6l2 2-1.3 1.3C4.5 9 1 5.5.7 2.3z" fill="#52b56d"/></svg>0415 672 903</li>
        <li><svg viewBox="0 0 10 10"><rect x="0.5" y="2" width="9" height="6.5" fill="#52b56d"/><path d="M0.5 2l4.5 3.5L9.5 2" stroke="#0f1f23" fill="none"/></svg>info@ridgewaybuild.com</li>
        <li><svg viewBox="0 0 10 10"><circle cx="5" cy="5" r="4.5" fill="#52b56d"/><path d="M0.5 5h9M5 .5c-2.5 2.5-2.5 6.5 0 9M5 .5c2.5 2.5 2.5 6.5 0 9" stroke="#0f1f23" stroke-width="0.7" fill="none"/></svg>www.<span class="accent">ridgewaybuild</span>.com</li>
      </ul>
    </div>
  </section>

  <section class="card card--back">
    <div class="wordmark wordmark--large">
      <span class="wordmark__square"></span>
      <span>Ridgeway<br>Construction</span>
    </div>
  </section>
</body>
</html>
```